Moxy Fen needs some awesome stationary

Do you have what it takes to get my brand? You either do or you don't, have a crack at a design and you my just win my business.

I don't want to waste your or my time, so put your creative genius on either a business card or envelope.

I however need a package of stationary that follows the same brand. I will message you to complete the remaining should I like your first submission.

Here is what I need, have a go!

Basically I need the following for my small business based in melbourne.
- Letterhead (printer ready and MS Word)
- Business Card
- Compliments Slip
- Envelope
- Proposal Cover Page (MS Word only)
- Presentation Folder
- Marbled Fox Cards
- Student Name Tent
- Index Cards
- Vell-Ka

I am establishing the brand and it must be modern, professional but also relaxed; that is not formal and not corporate. It represents a company are leaders, but small enough to care and operate like a bunch of friends. We are bringing people and conversations back to business, and turfing out all the bureaucracy and crazy and wasteful procedures. Its about "lets talk and figure it out together and find even better ways".

Target Market(s)

Mainly companies that build software products, but Agile practices are used in many other industries (even graphic design projects)

Industry/Entity Type

Information Technology

Font styles to use
Sans Serif

Colors
3176b5
aaaaaa

Requirements
Must have
• I like curves and circles and not boxes or rectangles.
• I want a colour rich design with my brand colours, but it must be balanced.
• I want more modern than traditional, but simple modern
Should not have
• Not corporate
• Please don't waste my time if your not going to think about it.
• Don't mess with my primary logo
• Don't change my colours
• Don't overlay logo on image

```html
<!DOCTYPE html>
<html lang="en">
<head>
<meta charset="utf-8">
<title>Moxy Fen — Sticky Notes</title>
<link href="https://fonts.googleapis.com/css2?family=Source+Sans+3:wght@400;700&display=swap" rel="stylesheet">
<style>
  :root {
    --backdrop: #898a8e;
    --note-yellow: #fbe14a;
    --ink: #1b1b1b;
    --note-shadow: rgba(0, 0, 0, 0.35);
  }
  * { margin: 0; padding: 0; box-sizing: border-box; }
  html, body {
    width: 1200px;
    height: 694px;
    overflow: hidden;
  }
  body {
    background: var(--backdrop);
    font-family: "Source Sans 3", "Helvetica Neue", Arial, sans-serif;
    color: var(--ink);
    position: relative;
  }
  .sticky-note {
    position: absolute;
    top: 168px;
    width: 358px;
    height: 359px;
    background: var(--note-yellow);
    box-shadow: 0 1px 4px var(--note-shadow);
  }
  .sticky-note--inline { left: 206px; }
  .sticky-note--stacked { left: 614px; }

  .brand-dot {
    position: absolute;
    border-radius: 50%;
    background: var(--ink);
  }
  .brand-name {
    position: absolute;
    font-weight: 700;
    color: var(--ink);
    white-space: nowrap;
    line-height: 1;
  }

  /* inline lockup */
  .sticky-note--inline .brand-dot {
    left: 22px;
    top: 277px;
    width: 20px;
    height: 20px;
  }
  .sticky-note--inline .brand-name {
    left: 50px;
    top: 277px;
    font-size: 19px;
  }

  /* stacked lockup */
  .sticky-note--stacked .brand-dot {
    left: 27px;
    top: 256px;
    width: 32px;
    height: 32px;
  }
  .sticky-note--stacked .brand-name {
    left: 26px;
    top: 292px;
    font-size: 11px;
  }

  .tagline {
    position: absolute;
    right: 23px;
    top: 280px;
    font-size: 13px;
    font-weight: 400;
    line-height: 1;
    white-space: nowrap;
  }
</style>
</head>
<body>
  <section class="sticky-note sticky-note--inline">
    <span class="brand-dot"></span>
    <span class="brand-name">Moxy Fen</span>
    <p class="tagline">Focus on getting done</p>
  </section>

  <section class="sticky-note sticky-note--stacked">
    <span class="brand-dot"></span>
    <span class="brand-name">Moxy Fen</span>
    <p class="tagline">Focus on getting done</p>
  </section>
</body>
</html>
```